Call Center In Need of Website Design

We are a call center that provides inbound and outbound calling & marketing services for eCommerce store. We would like to see a fun, creative, playful design that is simple.

Here are some sample design sites we like;
- https://www.velmoreline.com/
- https://pindrask.io/
- https://www.glimbertic.com/live-chat-software/
- https://www.zavrolin.com/

Here are some competitor sites;
- https://www.ostrevaglinks.com/
- https://www.helpkestrel.com/

I have attached website content for your use.

Target Market(s)

eCommerce

Coding

Coded - Design and coding required

Number of Pages Required

5+ page

Font styles to use
Sans Serif

Colors

Designer to choose colors to be used in the design.

Requirements
Must have
• Must have designs for the following 5 separate pages;
• 1. Home (landing)
• - This will be were the design style really needs to show.
• - Just needs to touch on key services
• - CTA
• 2. About Us
• - Basic page for about me paragraph
• 3. Services
• - List of services with icons
• - Click on service type to expand details or hover over service icon to view popup bubble with details about that service
• 4. Pricing
• - Option to bundle 1(one) digital service plan and 1(one) call center service plan
• - Bundling adds 10% monthly discount to over all price
• - Customer does NOT have to bundle
• - FAQ
• 5. Contact Us
• - Include a capture form (name, company name, email, phone, message)
• - Contact info
• - Business hours
• When customer purchases their desired plan, then they are taken to a page where they must schedule a call with an account rep.
Nice to have
• home page animations
Should not have
• All information on Home/Landing page.

```html
<!DOCTYPE html>
<html lang="en">
<head>
<meta charset="utf-8">
<title>Orbitra — Customer Care &amp; Back-End Office Support</title>
<link rel="stylesheet" href="https://fonts.googleapis.com/css2?family=Montserrat:wght@400;500;600&family=Roboto:wght@400;500;700&display=swap">
<style>
:root{
  --brand:#55b894;
  --brand-dark:#3fa07d;
  --ink:#111111;
  --text:#555555;
  --muted:#8a8a8a;
  --line:#dddddd;
  --card:#efefef;
  --footer:#1c1d1f;
  --footer-text:#d6d6d6;
  --white:#ffffff;
}
*{box-sizing:border-box;margin:0;padding:0}
html,body{width:1200px;height:2452px;overflow:hidden}
body{position:relative;background:var(--white);font-family:"Roboto",Arial,sans-serif;color:var(--text)}
.abs{position:absolute}
a{color:inherit;text-decoration:none}

/* header */
.site-header{left:0;top:0;width:1200px;height:98px;background:var(--white)}
.brand{left:98px;top:24px;display:flex;align-items:center;gap:14px}
.brand-dot{width:48px;height:48px;border:4px solid var(--brand);border-radius:50%}
.brand-name{font-family:"Montserrat",Arial,sans-serif;font-weight:500;font-size:28px;letter-spacing:6px;color:#333}
.main-nav{right:96px;top:38px;display:flex;gap:30px;align-items:center;font-family:"Roboto",Arial,sans-serif;font-weight:500;font-size:14px;color:#222}
.main-nav .active{color:var(--brand)}

/* hero */
.hero{left:0;top:98px;width:1200px;height:556px}
.hero-photo{position:absolute;inset:0;background:linear-gradient(90deg,#f4f5f6 0%,#eceef0 35%,#c9b7a6 60%,#a98a74 78%,#5f4a3f 100%)}
.hero-title{left:96px;top:250px;font-family:"Montserrat",Arial,sans-serif;font-weight:500;font-size:66px;line-height:1.1;letter-spacing:2px;color:var(--ink);white-space:nowrap}
.hero-lead{left:98px;top:342px;width:480px;font-size:22px;line-height:31px;color:#222}
.btn{display:inline-flex;align-items:center;justify-content:center;gap:8px;background:var(--brand);color:var(--white);font-family:"Roboto",Arial,sans-serif;font-weight:700;border-radius:30px;text-transform:uppercase;white-space:nowrap}
.hero-btn{left:98px;top:433px;width:208px;height:55px;font-size:18px}

/* about */
.about{left:0;top:654px;width:1200px;height:1409px;background:linear-gradient(180deg,#fbfbfb 0%,#f2f3f3 40%,#f6f6f6 75%,#ffffff 100%)}
.about-side{left:10px;top:1098px;transform:rotate(-90deg);transform-origin:0 0;font-family:"Montserrat",Arial,sans-serif;font-size:66px;line-height:1;font-weight:500;color:#e3e3e3;letter-spacing:2px;white-space:nowrap}
.about-title{left:98px;top:745px;font-family:"Montserrat",Arial,sans-serif;font-weight:500;font-size:34px;color:var(--ink);white-space:nowrap}
.about-copy{left:98px;top:812px;width:466px;font-size:13px;line-height:24px;text-align:justify}
.about-copy p+p{margin-top:17px}
.about-btn{left:98px;top:1014px;width:156px;height:46px;font-size:14px}
.video{left:626px;top:750px;width:484px;height:313px}
.video-frame{position:absolute;inset:0}
.video-photo{position:absolute;left:10px;top:12px;width:462px;height:289px;background:linear-gradient(120deg,#dfe3e6 0%,#c8ced2 45%,#b79c8a 70%,#8b6e5e 100%);border:3px solid #fff}
.divider{left:100px;top:1163px;width:1004px;height:1px;background:var(--line)}

/* what we do */
.wwd-ghost{left:0;top:1230px;width:1200px;text-align:center;font-family:"Montserrat",Arial,sans-serif;font-size:72px;font-weight:500;color:rgba(0,0,0,.08);white-space:nowrap}
.wwd-title{left:0;top:1254px;width:1200px;text-align:center;font-family:"Montserrat",Arial,sans-serif;font-size:34px;font-weight:500;color:var(--ink)}
.wwd-copy{left:205px;top:1324px;width:790px;text-align:center;font-size:13px;line-height:25px}
.wwd-tag{left:0;top:1418px;width:1200px;text-align:center;font-family:"Montserrat",Arial,sans-serif;font-size:23px;line-height:33px;color:var(--brand)}

.service-card{top:1534px;width:473px;height:428px;background:var(--card);overflow:hidden}
.card-digital{left:100px}
.card-call{left:634px}
.card-title{position:absolute;left:50px;top:44px;font-family:"Montserrat",Arial,sans-serif;font-size:26px;font-weight:500;color:var(--ink);white-space:nowrap}
.card-list{position:absolute;left:50px;top:112px;list-style:none}
.card-list li{display:flex;align-items:center;gap:18px;height:31.7px;font-size:14.5px;color:#444;white-space:nowrap}
.card-btn{position:absolute;left:52px;top:338px;height:36px;padding:0 22px;font-size:13px}
.card-art{position:absolute;border-radius:4px}
.headset-art{left:270px;top:30px;width:200px;height:320px;background:radial-gradient(ellipse at 50% 60%,#9a9a9a 0%,#5a5a5a 40%,rgba(239,239,239,0) 70%)}
.agent-art{left:260px;top:100px;width:213px;height:328px;background:radial-gradient(ellipse at 55% 55%,#d9b49a 0%,#c79a7d 30%,#f7f7f7 55%,rgba(239,239,239,0) 75%)}

/* footer */
.site-footer{left:0;top:2063px;width:1200px;height:389px;background:var(--footer);color:var(--footer-text)}
.foot-col{top:95px}
.foot-head{font-family:"Roboto",Arial,sans-serif;font-weight:500;font-size:17px;color:var(--white);text-transform:uppercase;margin-bottom:26px;white-space:nowrap}
.contact-list{list-style:none;font-size:12.5px;line-height:20px}
.contact-list li{display:flex;gap:16px;margin-bottom:18px;white-space:nowrap}
.contact-list svg{flex:none;margin-top:2px}
.link-list{list-style:none;font-size:12.5px}
.link-list li{height:28.5px;display:flex;gap:12px;white-space:nowrap}
.link-list li::before{content:"»";color:var(--footer-text)}
.news-copy{font-size:12.5px;line-height:21px;width:260px;margin-top:-6px}
.news-input{margin-top:12px;width:254px;height:34px;background:var(--white);color:#777;font-size:12px;display:flex;align-items:center;padding-left:14px}
.news-btn{margin-top:12px;width:112px;height:35px;font-size:14px}
.foot-rule{left:100px;top:313px;width:1004px;height:1px;background:#3b3c3e}
.copyright{left:100px;top:340px;font-size:13px;color:var(--white);white-space:nowrap}
.social{right:96px;top:332px;display:flex;gap:8px}
.social span{width:30px;height:30px;border:1.5px solid var(--white);border-radius:50%}
</style>
</head>
<body>

<header class="site-header abs">
  <div class="brand abs"><span class="brand-dot"></span><span class="brand-name">ORBITRA</span></div>
  <nav class="main-nav abs">
    <a class="active">HOME</a><a>ABOUT US</a><a>SERVICES</a><a>PRICING</a><a>CONTACT US</a>
    <svg width="14" height="14" viewBox="0 0 14 14" aria-label="Search"><circle cx="5.8" cy="5.8" r="4.3" fill="none" stroke="#222" stroke-width="2"/><line x1="9" y1="9" x2="13" y2="13" stroke="#222" stroke-width="2.2" stroke-linecap="round"/></svg>
  </nav>
</header>

<section class="hero abs">
  <div class="hero-photo" role="img" aria-label="Photo of smiling call centre agents wearing headsets"></div>
</section>
<h1 class="hero-title abs">ORBITRA</h1>
<p class="hero-lead abs">Orbitra is an omnichannel provider for customer care and back-end office support.</p>
<a class="btn hero-btn abs">Read More
  <svg width="17" height="17" viewBox="0 0 16 16"><circle cx="8" cy="8" r="8" fill="#fff"/><path d="M4 8h6M7.5 5l3 3-3 3" stroke="var(--brand)" stroke-width="2" fill="none"/></svg></a>

<section class="about abs" role="img" aria-label="Faint background photo of an office with headsets"></section>
<div class="about-side abs">ABOUT US</div>
<h2 class="about-title abs">WELCOME TO ORBITRA</h2>
<div class="about-copy abs">
  <p>Orbitra is an omnichannel provider for customer care and back-end office support. We primarily work with eCommerce companies around the world.</p>
  <p>Our service is vital to the core operations and functionality of consumer-focused online eCommerce companies. Orbitra originally started out as a generalized call center support company. Based in California, the founder quickly realized that there was a lack of support for eCommerce owners...</p>
</div>
<a class="btn about-btn abs">Read More
  <svg width="14" height="14" viewBox="0 0 16 16"><circle cx="8" cy="8" r="8" fill="#fff"/><path d="M4 8h6M7.5 5l3 3-3 3" stroke="var(--brand)" stroke-width="2" fill="none"/></svg></a>
<div class="video abs">
  <svg class="video-frame" width="484" height="313" viewBox="0 0 484 313">
    <path d="M1 55V1h55M428 1h55v54M483 258v54h-55M56 312H1v-54" fill="none" stroke="var(--brand)" stroke-width="3"/>
    <rect x="8" y="10" width="468" height="293" fill="none" stroke="#dcdcdc" stroke-width="1"/>
  </svg>
  <div class="video-photo" role="img" aria-label="Video still of an agent with a headset working at a computer in a bright office"></div>
</div>
<div class="divider abs"></div>

<div class="wwd-ghost abs">WHAT WE DO</div>
<h2 class="wwd-title abs">WHAT WE DO</h2>
<p class="wwd-copy abs">Orbitra is your personal customer service and product research team. We love eCommerce, but we love seeing business owners succeed even more! That is exactly why we have developed the processes and technology to take care of the most over looked areas in eCommerce - Customer Service and Retention.</p>
<p class="wwd-tag abs">Let Orbitra handle your customers while you focus on<br>growing your business.</p>

<article class="service-card card-digital abs">
  <div class="card-art headset-art" role="img" aria-label="Product photo of a call centre headset"></div>
  <h3 class="card-title">Digital Services</h3>
  <ul class="card-list">
    <li><svg width="13" height="13" viewBox="0 0 12 12"><circle cx="6" cy="6" r="6" fill="var(--brand)"/><path d="M5 3.5 7.5 6 5 8.5" stroke="#fff" stroke-width="1.6" fill="none"/></svg>Email Support</li>
    <li><svg width="13" height="13" viewBox="0 0 12 12"><circle cx="6" cy="6" r="6" fill="var(--brand)"/><path d="M5 3.5 7.5 6 5 8.5" stroke="#fff" stroke-width="1.6" fill="none"/></svg>Live Chat Support</li>
    <li><svg width="13" height="13" viewBox="0 0 12 12"><circle cx="6" cy="6" r="6" fill="var(--brand)"/><path d="M5 3.5 7.5 6 5 8.5" stroke="#fff" stroke-width="1.6" fill="none"/></svg>Product Research</li>
    <li><svg width="13" height="13" viewBox="0 0 12 12"><circle cx="6" cy="6" r="6" fill="var(--brand)"/><path d="M5 3.5 7.5 6 5 8.5" stroke="#fff" stroke-width="1.6" fill="none"/></svg>Product Listing</li>
    <li><svg width="13" height="13" viewBox="0 0 12 12"><circle cx="6" cy="6" r="6" fill="var(--brand)"/><path d="M5 3.5 7.5 6 5 8.5" stroke="#fff" stroke-width="1.6" fill="none"/></svg>Price Monitoring</li>
    <li><svg width="13" height="13" viewBox="0 0 12 12"><circle cx="6" cy="6" r="6" fill="var(--brand)"/><path d="M5 3.5 7.5 6 5 8.5" stroke="#fff" stroke-width="1.6" fill="none"/></svg>Product Photo &amp; Video Editing</li>
  </ul>
  <a class="btn card-btn">See Details
    <svg width="12" height="12" viewBox="0 0 16 16"><circle cx="8" cy="8" r="8" fill="#fff"/><path d="M4 8h6M7.5 5l3 3-3 3" stroke="var(--brand)" stroke-width="2" fill="none"/></svg></a>
</article>

<article class="service-card card-call abs">
  <div class="card-art agent-art" role="img" aria-label="Photo of a smiling customer service agent wearing a headset"></div>
  <h3 class="card-title">Call Center Services</h3>
  <ul class="card-list">
    <li><svg width="13" height="13" viewBox="0 0 12 12"><circle cx="6" cy="6" r="6" fill="var(--brand)"/><path d="M5 3.5 7.5 6 5 8.5" stroke="#fff" stroke-width="1.6" fill="none"/></svg>Answering service</li>
    <li><svg width="13" height="13" viewBox="0 0 12 12"><circle cx="6" cy="6" r="6" fill="var(--brand)"/><path d="M5 3.5 7.5 6 5 8.5" stroke="#fff" stroke-width="1.6" fill="none"/></svg>Welcome Calls</li>
    <li><svg width="13" height="13" viewBox="0 0 12 12"><circle cx="6" cy="6" r="6" fill="var(--brand)"/><path d="M5 3.5 7.5 6 5 8.5" stroke="#fff" stroke-width="1.6" fill="none"/></svg>Follow-Up Service</li>
    <li><svg width="13" height="13" viewBox="0 0 12 12"><circle cx="6" cy="6" r="6" fill="var(--brand)"/><path d="M5 3.5 7.5 6 5 8.5" stroke="#fff" stroke-width="1.6" fill="none"/></svg>Customer Upselling</li>
    <li><svg width="13" height="13" viewBox="0 0 12 12"><circle cx="6" cy="6" r="6" fill="var(--brand)"/><path d="M5 3.5 7.5 6 5 8.5" stroke="#fff" stroke-width="1.6" fill="none"/></svg>Over-The-Phone Order Taking</li>
    <li><svg width="13" height="13" viewBox="0 0 12 12"><circle cx="6" cy="6" r="6" fill="var(--brand)"/><path d="M5 3.5 7.5 6 5 8.5" stroke="#fff" stroke-width="1.6" fill="none"/></svg>Order Return Processing</li>
  </ul>
  <a class="btn card-btn">View All Services
    <svg width="12" height="12" viewBox="0 0 16 16"><circle cx="8" cy="8" r="8" fill="#fff"/><path d="M4 8h6M7.5 5l3 3-3 3" stroke="var(--brand)" stroke-width="2" fill="none"/></svg></a>
</article>

<footer class="site-footer abs">
  <div class="foot-col abs" style="left:100px">
    <h4 class="foot-head">Contact Us</h4>
    <ul class="contact-list">
      <li><svg width="10" height="14" viewBox="0 0 10 14"><path d="M5 0a5 5 0 0 0-5 5c0 3.5 5 9 5 9s5-5.5 5-9a5 5 0 0 0-5-5z" fill="#fff"/><circle cx="5" cy="5" r="1.8" fill="var(--footer)"/></svg><span>Orbitra, Inc.<br>418 Calloway Ave. Marlow, CA 93650</span></li>
      <li><svg width="13" height="13" viewBox="0 0 24 24"><path d="M6.6 10.8a15.1 15.1 0 0 0 6.6 6.6l2.2-2.2a1 1 0 0 1 1-.25 11.4 11.4 0 0 0 3.6.57 1 1 0 0 1 1 1V20a1 1 0 0 1-1 1A17 17 0 0 1 3 4a1 1 0 0 1 1-1h3.5a1 1 0 0 1 1 1c0 1.25.2 2.45.57 3.57a1 1 0 0 1-.25 1z" fill="#fff"/></svg><span>(800) 555-0147</span></li>
      <li><svg width="15" height="12" viewBox="0 0 15 12"><rect width="15" height="12" rx="1" fill="#fff"/><path d="M0.5 1 7.5 6.5 14.5 1" stroke="var(--footer)" stroke-width="1.4" fill="none"/></svg><span>hello@orbitra-support.com</span></li>
    </ul>
  </div>
  <div class="foot-col abs" style="left:428px">
    <h4 class="foot-head">Categories</h4>
    <ul class="link-list"><li>Home</li><li>About Us</li><li>Services</li><li>Pricing</li><li>Contact Us</li></ul>
  </div>
  <div class="foot-col abs" style="left:621px">
    <h4 class="foot-head">Support</h4>
    <ul class="link-list"><li>Digital Services</li><li>Call Center Services</li><li>FAQs</li><li>Privacy Policy</li><li>Terms Of Services</li></ul>
  </div>
  <div class="foot-col abs" style="left:846px">
    <h4 class="foot-head">Newsletter Subscription</h4>
    <p class="news-copy">Register your Email Address to get more Information about us</p>
    <div class="news-input">Email Address</div>
    <a class="btn news-btn">Subscribe</a>
  </div>
  <div class="foot-rule abs"></div>
  <p class="copyright abs">Copyrights © 2018 Orbitra.&nbsp; All Rights Reserved.</p>
  <div class="social abs" aria-label="Social links"><span></span><span></span><span></span><span></span></div>
</footer>

</body>
</html>
```